Hi Designers,

I will need 4 web pages designed. The web page looks like an App (if you click on the logo, or the icon on an iPad, it will take you to the website), but it is still a webpage.

Please check the attachment on this brief to understand what specific pages I need to be designed.

A .PSD (straight-up PhotoShop image) as final deliverable is fine, as long as you give us the exact “web color numbers”.

The design is for desktop and iPad but in a single unified web application, NOT separate web app and (native) iPad app.

Details:

Brightwater Policy Partners is developing a browser-based application for use on any mobile device or desktop. The app will be used by corporations to communicate with their employees regarding legal, regulatory and company requirements for conducting business. The app is known as “Harbor Guidance Portal.” When the user clicks on the icon for Harbor Guidance Portal, they will enter a site full of information that a company deems necessary for the employee to do his/her job. There are several content sections within the site, including a login page, training, policies, forms, news feeds and blogs.

The application has been built using Microsoft .NET, and fully supports CSS-type skinning; it uses traditional page layouts. We are seeking a product logo concept (image), a master application/desktop icon (image), as well as a full color scheme/theme/skin design for all areas of the application (header area, body text, menu bar, etc.) in the form of a CSS. The look should be clean, crisp and professional; nothing cartoony or whimsical. It should be easy to read and “airy”.

We have sketched prototypes for the basic application page layout that we can send as a next step of the process.
Updates

Screen shots have been uploaded to this project.  Please use them to guide your design.

Dear designers,

I apologize for the delay in providing feedback. My partners and I will provide feedback in a few days. Thank you for your patience.

Industry/Entity Type

Business

Font styles to use
Other font styles liked:
• see font on screen shots when uploaded

```html
<!DOCTYPE html>
<html lang="en">
<head>
<meta charset="utf-8">
<title>Harbor Guidance Portal – Sign in</title>
<link rel="stylesheet" href="https://fonts.googleapis.com/css2?family=Source+Sans+3:wght@400;600&display=swap">
<style>
  :root {
    --navy: #042a4f;
    --page: #ffffff;
    --panel: #eeefee;
    --panel-border: #d9dbd9;
    --field-border: #d3d6d6;
    --text: #3a3f44;
    --label: #4a4f54;
    --footer-text: #e6ecf2;
    --button: #6b9e8d;
    --accent-blue: #1a93c8;
    --social-one: #3b5998;
    --social-two: #2fa3d8;
    --social-three: #f26a1b;
    --social-four: #e22b2f;
  }
  * { box-sizing: border-box; margin: 0; padding: 0; }
  html, body { width: 1200px; height: 682px; overflow: hidden; }
  body {
    position: relative;
    background: var(--page);
    font-family: "Source Sans 3", sans-serif;
    color: var(--text);
  }
  .site-header {
    position: absolute; left: 0; top: 0; width: 1200px; height: 100px;
    background: var(--navy);
  }
  .brand {
    position: absolute; left: 98px; top: 41px;
    display: flex; align-items: center; gap: 10px;
    color: #ffffff; font-size: 12px; font-weight: 600;
  }
  .brand-dot {
    width: 18px; height: 18px; border-radius: 50%;
    background: var(--accent-blue);
  }
  .login-panel {
    position: absolute; left: 260px; top: 144px; width: 682px; height: 312px;
    background: var(--panel); border: 1px solid var(--panel-border); border-radius: 4px;
  }
  .field-label {
    position: absolute; right: 497px; font-size: 17px; color: var(--label);
    line-height: 20px;
  }
  .field-label.user { top: 63px; }
  .field-label.pass { top: 138px; }
  .field-input {
    position: absolute; left: 220px; width: 389px; height: 52px;
    background: #ffffff; border: 1px solid var(--field-border); border-radius: 4px;
  }
  .field-input.user { top: 46px; }
  .field-input.pass { top: 121px; height: 51px; }
  .remember {
    position: absolute; left: 225px; top: 206px;
    display: flex; align-items: center; gap: 12px; font-size: 15px;
  }
  .checkbox {
    width: 14px; height: 14px; background: #fff;
    border: 1px solid #8a8f94; border-radius: 2px;
  }
  .forgot {
    position: absolute; right: 72px; top: 205px; font-size: 15px; color: var(--text);
  }
  .sign-in {
    position: absolute; left: 496px; top: 249px; width: 112px; height: 41px;
    background: var(--button); border-radius: 3px; color: #fff;
    display: flex; align-items: center; justify-content: center; gap: 14px;
    font-size: 18px; font-weight: 600;
  }
  .product-mark {
    position: absolute; left: 448px; top: 495px;
    display: flex; align-items: center; gap: 19px;
    font-size: 19px; color: var(--text);
  }
  .product-dot {
    width: 44px; height: 44px; border-radius: 50%; background: var(--accent-blue);
  }
  .site-footer {
    position: absolute; left: 0; top: 577px; width: 1200px; height: 105px;
    background: var(--navy); color: var(--footer-text); font-size: 13px;
  }
  .footer-links { position: absolute; left: 85px; top: 27px; }
  .copyright { position: absolute; left: 85px; top: 61px; }
  .social-list { position: absolute; left: 930px; top: 35px; display: flex; gap: 13px; }
  .social-tile { width: 36px; height: 36px; }
  .social-tile.one { background: var(--social-one); }
  .social-tile.two { background: var(--social-two); }
  .social-tile.three { background: var(--social-three); }
  .social-tile.four { background: var(--social-four); }
</style>
</head>
<body>
  <header class="site-header">
    <div class="brand"><span class="brand-dot"></span><span>Corvane Labs</span></div>
  </header>

  <main>
    <form class="login-panel">
      <span class="field-label user">User Name:</span>
      <div class="field-input user"></div>
      <span class="field-label pass">Password:</span>
      <div class="field-input pass"></div>
      <div class="remember"><span class="checkbox"></span><span>Keep my signed in</span></div>
      <span class="forgot">Forgot my password!</span>
      <div class="sign-in">
        <svg width="16" height="19" viewBox="0 0 16 19" aria-hidden="true">
          <path d="M4 8V5.5a4 4 0 0 1 8 0V8" fill="none" stroke="#fff" stroke-width="2.4"/>
          <rect x="1" y="8" width="14" height="10" rx="1.5" fill="#fff"/>
        </svg>
        <span>Sign in</span>
      </div>
    </form>

    <div class="product-mark"><span class="product-dot"></span><span>Harbor Guidance Portal</span></div>
  </main>

  <footer class="site-footer">
    <p class="footer-links">Terms and conditions | Privacy Policy</p>
    <p class="copyright">Copyright 2013.&nbsp; All rights reserved.</p>
    <div class="social-list">
      <span class="social-tile one"></span>
      <span class="social-tile two"></span>
      <span class="social-tile three"></span>
      <span class="social-tile four"></span>
    </div>
  </footer>
</body>
</html>
```